Estate Planning Law Firm opening new branch in Florida

I am an experienced estate planning attorney that recently relocated to Florida. Looking for a banner Ad to place on platforms such as Porchvine, Chatterbox and Picturely to create publicity for firm and new leads.

```html
<!DOCTYPE html>
<html lang="en">
<head>
<meta charset="utf-8">
<title>Serenova Law Firm – Florida Banner Ads</title>
<link href="https://fonts.googleapis.com/css2?family=Montserrat:wght@400;500;600;800;900&family=Oswald:wght@500&display=swap" rel="stylesheet">
<style>
  :root{
    --board:#03141f;
    --navy-top:#0b3657;
    --navy-mid:#144a70;
    --navy-deep:#0a2a44;
    --ink:#2a2a2a;
    --ink-blue:#113a5e;
    --grey:#7f8790;
    --grey-light:#9aa8b4;
    --teal:#1f6f69;
    --teal-dark:#17564f;
    --ring:#2d4455;
    --badge-bg:#e3e7ea;
    --white:#ffffff;
    --rule:#b9bec3;
    --label:#5fd0df;
    --moon-glow:#ffcf5a;
  }
  *{box-sizing:border-box;margin:0;padding:0}
  html,body{width:1200px;height:1200px;overflow:hidden}
  body{background:var(--board);font-family:"Montserrat",Arial,sans-serif;position:relative}

  .ad{position:absolute;overflow:hidden;background:var(--white)}
  .ad > *{position:absolute}
  .ad-label{position:absolute;color:var(--label);font-size:12px;font-weight:600;letter-spacing:.32em;text-transform:uppercase}

  .photo-city{background:linear-gradient(180deg,#0f3a5a 0%,#1b3d57 35%,#4c4438 62%,#1f3850 80%,#0e2a44 100%)}
  .photo-couple{background:linear-gradient(160deg,#3b3a3e 0%,#2a3446 45%,#1d2a3d 100%)}

  .relocated{color:var(--white);font-weight:500;line-height:.95;text-transform:uppercase;white-space:nowrap}
  .florida{color:var(--white);font-weight:900;letter-spacing:.01em;line-height:1;white-space:nowrap}
  .moon{display:inline-block;width:.74em;height:.74em;border-radius:50%;color:transparent;vertical-align:-.02em;
        background:radial-gradient(circle,#fff 62%,#fff7dc 78%,#ffe2a0 100%);
        box-shadow:0 0 .25em .08em var(--moon-glow),0 0 .6em .1em rgba(255,207,90,.45)}

  .welcome{color:var(--grey);font-weight:500;text-transform:uppercase;line-height:.95;white-space:nowrap}
  .headline{font-weight:900;text-transform:uppercase;line-height:.88;white-space:nowrap}
  .cta{background:var(--teal);color:var(--white);font-weight:800;text-transform:uppercase;display:flex;align-items:center;justify-content:center;border-radius:0 14px 14px 0;white-space:nowrap}

  .badge{border-radius:50%;background:radial-gradient(circle,#f4f6f7 55%,var(--badge-bg) 80%,#c7cdd2 100%);border:1px solid #c3c9ce;display:flex;align-items:center;justify-content:center;transform:translate(-50%,-50%)}
  .badge-core{border-radius:50%;background:radial-gradient(circle at 50% 40%,#22807a,var(--teal-dark));box-shadow:0 0 0 3px #f3f5f6,0 0 0 5px var(--ring);display:flex;align-items:center;justify-content:center;text-align:center;color:var(--white);font-family:"Oswald","Arial Narrow",sans-serif;font-weight:500;text-transform:uppercase;line-height:1.1}

  .firm{display:flex;align-items:center;gap:6px;color:var(--ink-blue)}
  .firm-mark{background:var(--teal);flex:none}
  .firm-text{display:flex;flex-direction:column;align-items:center;line-height:1}
  .firm-name{font-weight:600;letter-spacing:.02em}
  .firm-sub{font-weight:500;letter-spacing:.04em;border-top:1px solid var(--ink-blue);padding-top:2px;margin-top:2px}

  .phone{color:var(--ink-blue);font-weight:800;white-space:nowrap}
  .web{color:var(--ink);font-weight:500;white-space:nowrap;letter-spacing:.02em}
  .rule{height:2px;background:var(--rule)}

  /* Porchvine wide ad */
  .ad-porchvine{left:323px;top:117px;width:699px;height:366px}
  .ad-porchvine .sky{left:0;top:0;width:293px;height:366px;background:linear-gradient(180deg,var(--navy-top),var(--navy-mid) 60%,var(--navy-deep))}
  .ad-porchvine .photo-city{left:0;top:165px;width:293px;height:201px}
  .ad-porchvine .photo-couple{left:118px;top:122px;width:228px;height:244px;border-radius:60px 60px 0 0}
  .ad-porchvine .relocated{left:35px;top:32px;font-size:20px}
  .ad-porchvine .florida{left:35px;top:76px;font-size:41.5px}
  .ad-porchvine .welcome{left:369px;top:29px;font-size:18px}
  .ad-porchvine .headline{left:368px;top:48px;font-size:28px;color:var(--ink)}
  .ad-porchvine .cta{left:375px;top:108px;width:220px;height:26px;font-size:17px}
  .ad-porchvine .rule-top{left:352px;top:150px;width:299px}
  .ad-porchvine .rule-bottom{left:352px;top:267px;width:299px}
  .ad-porchvine .badge{width:88px;height:88px;top:206px}
  .ad-porchvine .badge-core{width:62px;height:62px;font-size:11.5px}
  .ad-porchvine .firm{left:352px;top:290px}
  .ad-porchvine .firm-mark{width:14px;height:14px}
  .ad-porchvine .firm-name{font-size:19px}
  .ad-porchvine .firm-sub{font-size:6.5px}
  .ad-porchvine .phone{left:500px;top:284px;font-size:21px}
  .ad-porchvine .web{left:500px;top:310px;font-size:9px}

  /* Chatterbox square ad */
  .ad-chatterbox{left:154px;top:575px;width:412px;height:412px;background:linear-gradient(180deg,var(--navy-top),var(--navy-mid) 40%,var(--navy-deep))}
  .ad-chatterbox .white-base{left:0;top:255px;width:412px;height:157px;background:var(--white)}
  .ad-chatterbox .photo-city{left:0;top:139px;width:412px;height:116px}
  .ad-chatterbox .photo-couple{left:219px;top:158px;width:193px;height:254px;border-radius:50px 50px 0 0}
  .ad-chatterbox .welcome{left:51px;top:21px;font-size:16px;color:var(--grey-light)}
  .ad-chatterbox .headline{left:51px;top:52px;font-size:21.5px;line-height:.89;color:var(--white)}
  .ad-chatterbox .relocated{left:251px;top:25px;font-size:13.4px}
  .ad-chatterbox .florida{left:251px;top:53px;font-size:28px}
  .ad-chatterbox .badge{width:54px;height:54px;top:253px}
  .ad-chatterbox .badge-core{width:38px;height:38px;font-size:6.5px}
  .ad-chatterbox .firm{left:35px;top:293px}
  .ad-chatterbox .firm-mark{width:14px;height:14px}
  .ad-chatterbox .firm-name{font-size:22px}
  .ad-chatterbox .firm-sub{font-size:7px}
  .ad-chatterbox .cta{left:36px;top:338px;width:150px;height:17px;font-size:11.5px;border-radius:0 9px 9px 0}
  .ad-chatterbox .phone{left:36px;top:361px;font-size:19px}
  .ad-chatterbox .web{left:38px;top:383px;font-size:8.5px}

  /* Picturely portrait ad */
  .ad-picturely{left:617px;top:569px;width:412px;height:516px;background:linear-gradient(180deg,var(--navy-top),var(--navy-mid) 35%,var(--navy-deep))}
  .ad-picturely .white-base{left:0;top:344px;width:412px;height:172px;background:var(--white)}
  .ad-picturely .photo-city{left:0;top:163px;width:412px;height:181px}
  .ad-picturely .photo-couple{left:200px;top:250px;width:212px;height:266px;border-radius:55px 55px 0 0}
  .ad-picturely .welcome{left:56px;top:30px;font-size:18px;color:var(--grey-light)}
  .ad-picturely .headline{left:56px;top:64px;font-size:24px;line-height:.9;color:var(--white)}
  .ad-picturely .relocated{left:250px;top:45px;font-size:14px}
  .ad-picturely .florida{left:250px;top:77px;font-size:27.5px}
  .ad-picturely .badge{width:50px;height:50px;top:341px}
  .ad-picturely .badge-core{width:35px;height:35px;font-size:6px}
  .ad-picturely .firm{left:36px;top:390px}
  .ad-picturely .firm-mark{width:13px;height:13px}
  .ad-picturely .firm-name{font-size:20px}
  .ad-picturely .firm-sub{font-size:6.5px}
  .ad-picturely .cta{left:38px;top:434px;width:154px;height:18px;font-size:11.5px;border-radius:0 9px 9px 0}
  .ad-picturely .phone{left:39px;top:458px;font-size:20px}
  .ad-picturely .web{left:40px;top:481px;font-size:8.5px}
</style>
</head>
<body>

<section class="ad ad-porchvine" aria-label="Porchvine banner ad">
  <div class="sky"></div>
  <div class="photo-city" role="img" aria-label="Night city skyline reflected on water"></div>
  <div class="photo-couple" role="img" aria-label="Portrait of the two attorneys smiling together"></div>
  <p class="relocated">Recently<br>relocated to</p>
  <p class="florida">FL<span class="moon">O</span>RIDA</p>
  <p class="welcome">Welcome to your trusted</p>
  <h1 class="headline">Estate planning<br>expert attorney</h1>
  <div class="cta">Book a call today</div>
  <div class="rule rule-top"></div>
  <div class="badge" style="left:397px"><div class="badge-core">Estate<br>planning</div></div>
  <div class="badge" style="left:504px"><div class="badge-core">Tax<br>planning</div></div>
  <div class="badge" style="left:608px"><div class="badge-core">Financial<br>planning</div></div>
  <div class="rule rule-bottom"></div>
  <div class="firm"><span class="firm-mark"></span><span class="firm-text"><span class="firm-name">SERENOVA</span><span class="firm-sub">LAW FIRM, PLLC</span></span></div>
  <p class="phone">(555) 014 2280</p>
  <p class="web">www.shieldandgrowestate.com</p>
</section>
<p class="ad-label" style="right:176px;top:501px">Porchvine banner ad</p>

<section class="ad ad-chatterbox" aria-label="Chatterbox banner ad">
  <div class="white-base"></div>
  <div class="photo-city" role="img" aria-label="Night city skyline reflected on water"></div>
  <div class="photo-couple" role="img" aria-label="Portrait of the two attorneys smiling together"></div>
  <p class="welcome">Welcome to<br>your trusted</p>
  <h2 class="headline">Estate<br>planning<br>expert<br>attorney</h2>
  <p class="relocated">Recently<br>relocated to</p>
  <p class="florida">FL<span class="moon">O</span>RIDA</p>
  <div class="badge" style="left:52px"><div class="badge-core">Financial<br>planning</div></div>
  <div class="badge" style="left:120px"><div class="badge-core">Tax<br>planning</div></div>
  <div class="badge" style="left:186px"><div class="badge-core">Estate<br>planning</div></div>
  <div class="firm"><span class="firm-mark"></span><span class="firm-text"><span class="firm-name">SERENOVA</span><span class="firm-sub">LAW FIRM, PLLC</span></span></div>
  <div class="cta">Book a call today</div>
  <p class="phone">(555) 014 2280</p>
  <p class="web">www.shieldandgrowestate.com</p>
</section>
<p class="ad-label" style="left:156px;top:1002px">Chatterbox banner ad</p>

<section class="ad ad-picturely" aria-label="Picturely banner ad">
  <div class="white-base"></div>
  <div class="photo-city" role="img" aria-label="Night city skyline reflected on water"></div>
  <div class="photo-couple" role="img" aria-label="Portrait of the two attorneys smiling together"></div>
  <p class="welcome">Welcome to<br>your trusted</p>
  <h2 class="headline">Estate<br>planning<br>expert<br>attorney</h2>
  <p class="relocated">Recently<br>relocated to</p>
  <p class="florida">FL<span class="moon">O</span>RIDA</p>
  <div class="badge" style="left:53px"><div class="badge-core">Financial<br>planning</div></div>
  <div class="badge" style="left:115px"><div class="badge-core">Tax<br>planning</div></div>
  <div class="badge" style="left:176px"><div class="badge-core">Estate<br>planning</div></div>
  <div class="firm"><span class="firm-mark"></span><span class="firm-text"><span class="firm-name">SERENOVA</span><span class="firm-sub">LAW FIRM, PLLC</span></span></div>
  <div class="cta">Book a call today</div>
  <p class="phone">(555) 014 2280</p>
  <p class="web">www.shieldandgrowestate.com</p>
</section>
<p class="ad-label" style="right:171px;top:1101px">Picturely banner ad</p>

</body>
</html>
```